Valdo Capital

We need a corporate style website design for a new company based in Shenzhen's Qianhai Special Economic Development Zone, China. We provide a range of financial services to large international investment companies. Typically these companies invest over 5 million RMB. The company is part of a group that consists of NorthKilns, ValdoTrusts and ValdoEquity. Our location and gateway into Qianhai Special Economic Zone is our core advantage. We would like to see designs that Do Not use purple and orange. The website design should be similar to other websites in this family but different enough to give it a unique style (See attached website links for reference). The final design should communicate financial safety and growth. This website will act partly as a business chamber with connections to the government so we would like it to be diplomatic in style.

www.northkilns.example
www.valdotrusts.example

*Nevegation Bar
Should including Homepage, Financial Product, Team, News.
Could refer to www.valdotrusts.example

*Contact Details

Miss Lan
Address:E 728, North Block, KMO Centre, East Sector, Shenzhen Bright Science Campus
Telephone: +86 0755 63920417
Cellphone: +86 13957280316

* Social Media
Should be grouped like:
1. Weibo QRcode+ Weibo
2. Facebook, Chirpline, Linkedin.

Industry/Entity Type

Investment

```html
<!DOCTYPE html>
<html lang="en">
<head>
<meta charset="utf-8">
<title>Valdo Capital</title>
<link href="https://fonts.googleapis.com/css2?family=Open+Sans:wght@400;600;700&display=swap" rel="stylesheet">
<style>
:root{
  --blue:#1c8ed8;
  --navy:#173a68;
  --navy-deep:#0f2a4f;
  --yellow:#f6c300;
  --ink:#333b45;
  --muted:#6d7681;
  --line:#dfe4ea;
  --paper:#ffffff;
  --page:#eef1f4;
}
*{box-sizing:border-box;margin:0;padding:0}
html,body{width:820px;height:1200px;overflow:hidden;background:var(--page)}
body{font-family:"Open Sans",Arial,sans-serif;color:var(--ink)}
.site{position:relative;width:820px;height:1200px;background:var(--paper);overflow:hidden}

.header{position:absolute;top:0;left:0;width:820px;height:40px;display:flex;align-items:center;justify-content:space-between;padding:0 60px;background:var(--paper)}
.brand{display:flex;align-items:center;gap:7px;font-size:13px;font-weight:700;color:var(--navy)}
.brand-mark{width:14px;height:14px;background:var(--blue)}
.nav{display:flex;gap:2px}
.nav a{font-size:8px;font-weight:600;color:var(--ink);text-decoration:none;padding:6px 8px;text-transform:uppercase}
.nav a.active{background:var(--blue);color:#fff}

.hero{position:absolute;top:40px;left:0;width:820px;height:240px;background:linear-gradient(180deg,#2f9be0 0%,#7cc4ef 45%,#c9b27a 78%,#a9865a 100%)}
.hero-caption{position:absolute;top:52px;left:410px;width:300px;color:#fff;font-size:15px;font-weight:600;line-height:1.35;background:rgba(20,110,180,.55);padding:8px 12px}
.hero-arrow{position:absolute;top:106px;width:20px;height:26px;background:var(--yellow);display:flex;align-items:center;justify-content:center}
.hero-arrow.prev{left:0}.hero-arrow.next{right:0}

.features{position:absolute;top:240px;left:60px;width:700px;display:flex;justify-content:space-between}
.feature{width:200px;text-align:center}
.feature-icon{width:34px;height:34px;border-radius:50%;background:var(--paper);border:3px solid var(--blue);margin:0 auto -8px;position:relative;display:flex;align-items:center;justify-content:center}
.feature-title{background:var(--blue);color:#fff;font-size:10px;font-weight:700;padding:12px 0 5px}
.feature-body{background:var(--paper);border:1px solid var(--line);border-top:none;padding:10px 12px 14px;font-size:7px;line-height:1.6;color:var(--muted);text-align:left}
.feature-body a{display:block;margin-top:6px;color:var(--blue);font-weight:600;text-decoration:none}

.intro{position:absolute;top:540px;left:60px;width:700px;font-size:7px;line-height:1.65;color:var(--muted)}
.intro-top{margin-bottom:8px}
.intro-row{display:flex;gap:16px}
.intro-photo{flex:0 0 170px;height:150px;background:linear-gradient(135deg,#d8c2a0,#8a6e4c 60%,#3d4a5a)}
.intro-row p{flex:1}
.rule{position:absolute;top:745px;left:60px;width:700px;height:3px;background:var(--blue)}

.section-title{font-size:10px;font-weight:700;color:var(--blue);text-transform:uppercase;padding-bottom:5px;border-bottom:1px solid var(--line);margin-bottom:10px}
.updates{position:absolute;top:785px;left:60px;width:320px}
.tweet{display:flex;gap:10px;margin-bottom:10px;font-size:7px;line-height:1.55;color:var(--muted)}
.tweet-thumb{flex:0 0 34px;height:30px;background:linear-gradient(135deg,#9fb8cf,#5a7690)}
.testimonials{position:absolute;top:785px;left:420px;width:340px}
.quote{display:flex;gap:12px;border:1px solid var(--line);padding:10px;font-size:7px;line-height:1.6;color:var(--muted)}
.quote-photo{flex:0 0 84px;height:94px;background:linear-gradient(160deg,#e3d0bd,#a88a72 55%,#3b4650)}
.quote-author{text-align:right;color:var(--blue);font-weight:600;font-size:7px;margin-top:6px}

.footer{position:absolute;top:1012px;left:0;width:820px;height:158px;background:var(--navy);border-top:3px solid var(--yellow);color:#d7e2f0;padding:14px 60px 0;display:flex;justify-content:space-between}
.footer h3{font-size:10px;font-weight:700;color:#fff;text-transform:uppercase;margin-bottom:9px}
.contact{width:200px;font-size:7px;line-height:1.6}
.contact p{margin-bottom:4px}
.newsletter{width:220px;font-size:7px;line-height:1.6}
.field{background:#fff;height:16px;margin-bottom:5px;font-size:7px;color:#9aa3ad;padding:3px 6px}
.news-form{display:flex;margin:8px 0}
.news-form .field{flex:1;margin:0}
.btn{background:var(--yellow);color:var(--navy);font-size:7px;font-weight:700;padding:3px 10px;display:inline-block;text-transform:uppercase}
.news-links{margin-top:4px;color:#fff}
.info{width:190px}
.info .area{height:34px}
.info-submit{text-align:right}

.bottom{position:absolute;top:1170px;left:0;width:820px;height:30px;background:var(--navy-deep);display:flex;align-items:center;justify-content:space-between;padding:0 60px;font-size:7px;color:#b7c5d8}
.social{display:flex;gap:8px}
.social span{width:14px;height:14px;border-radius:50%;background:#3f6190}
</style>
</head>
<body>
<div class="site">

  <header class="header">
    <div class="brand"><span class="brand-mark"></span>Valdo Capital</div>
    <nav class="nav">
      <a class="active" href="#">Home</a>
      <a href="#">About Us</a>
      <a href="#">Financial Product</a>
      <a href="#">Team</a>
      <a href="#">News</a>
      <a href="#">Contact Us</a>
    </nav>
  </header>

  <section class="hero" role="img" aria-label="Hand placing coins on rising stacks of coins against a blue sky">
    <p class="hero-caption">Consectetur adipisicing elit, sed do eiusmod tempor incididunt ut labore</p>
    <span class="hero-arrow prev"><svg width="8" height="10" viewBox="0 0 8 10"><path d="M6 1 2 5l4 4" fill="none" stroke="#fff" stroke-width="2"/></svg></span>
    <span class="hero-arrow next"><svg width="8" height="10" viewBox="0 0 8 10"><path d="M2 1l4 4-4 4" fill="none" stroke="#fff" stroke-width="2"/></svg></span>
  </section>

  <section class="features">
    <article class="feature">
      <div class="feature-icon"><svg width="14" height="14" viewBox="0 0 14 14"><circle cx="7" cy="7" r="6" fill="none" stroke="#1c8ed8" stroke-width="1.5"/><path d="M7 6v4M7 4v.5" stroke="#1c8ed8" stroke-width="1.5"/></svg></div>
      <h2 class="feature-title">ABOUT US</h2>
      <div class="feature-body">Our firm helps large investors enter the Qianhai zone with safe, steady and well guided capital plans. We offer careful advice, clear terms and long term support for every partner.<a href="#">Read more</a></div>
    </article>
    <article class="feature">
      <div class="feature-icon"><svg width="14" height="14" viewBox="0 0 14 14"><circle cx="7" cy="5" r="2.5" fill="#1c8ed8"/><path d="M2 13c0-3 2.5-5 5-5s5 2 5 5" fill="#1c8ed8"/></svg></div>
      <h2 class="feature-title">TEAM</h2>
      <div class="feature-body">Our team brings years of work in banking, trade and public policy. Each member knows the local rules well and guides clients through every step with care and trust.<a href="#">Read more</a></div>
    </article>
    <article class="feature">
      <div class="feature-icon"><svg width="14" height="14" viewBox="0 0 14 14"><rect x="2" y="3" width="10" height="8" fill="none" stroke="#1c8ed8" stroke-width="1.5"/><path d="M4 6h6M4 8h4" stroke="#1c8ed8"/></svg></div>
      <h2 class="feature-title">NEWS</h2>
      <div class="feature-body">Read the latest updates on new funds, zone policies and market trends. We share short notes each week so partners can plan ahead with clear and current facts.<a href="#">Read more</a></div>
    </article>
  </section>

  <section class="intro">
    <p class="intro-top">Valdo Capital is a member of a trusted group of financial firms based in Shenzhen. We serve international investment companies that place large sums into the Qianhai zone, and we act as a bridge between investors, local partners and public offices. Our location gives clients direct access to the zone and its growing network of services.</p>
    <div class="intro-row">
      <div class="intro-photo" role="img" aria-label="Businessman holding banknotes"></div>
      <p>We believe that sound finance rests on patience, clear rules and honest advice. Every plan we build starts with a careful review of goals and risks, followed by steady guidance over the full life of the investment. Our partners value the calm and diplomatic way we work with both private firms and government bodies. With offices close to the heart of the zone, we can meet clients quickly, answer questions in person and help them open doors that would otherwise take months. We look forward to building long and fruitful partnerships with investors who share our view of safe and lasting growth in southern China.</p>
    </div>
  </section>
  <div class="rule"></div>

  <section class="updates">
    <h2 class="section-title">Chirpline</h2>
    <div class="tweet"><div class="tweet-thumb" role="img" aria-label="Post thumbnail"></div><p>New policy notes on cross border funds in the Qianhai zone are now online for all partners to read.</p></div>
    <div class="tweet"><div class="tweet-thumb" role="img" aria-label="Post thumbnail"></div><p>Our team joined the regional finance forum this week to discuss steady growth and safe capital flows.</p></div>
    <div class="tweet"><div class="tweet-thumb" role="img" aria-label="Post thumbnail"></div><p>Thank you to all partners who visited our new office in Shenzhen this month.</p></div>
  </section>

  <section class="testimonials">
    <h2 class="section-title">Testimonials</h2>
    <div class="quote">
      <div class="quote-photo" role="img" aria-label="Portrait of a client"></div>
      <div>
        <p>"Working with this team has been calm, clear and rewarding from the first meeting. They explained every rule of the zone in plain words, kept us informed at each stage and helped us reach local partners we could not have found alone. Our investment has grown steadily and we feel safe knowing they watch over it with such care."</p>
        <p class="quote-author">- Client Name</p>
      </div>
    </div>
  </section>

  <footer class="footer">
    <div class="contact">
      <h3>Contact</h3>
      <p>+86 0755 4100 2200 (Phone)</p>
      <p>+86 0755 4100 2201 (Fax)</p>
      <p>hello@valdocapital.example</p>
      <p>Street Address<br>Your Street Name<br>Town City, Your State</p>
    </div>
    <div class="newsletter">
      <h3>Subscribe to our newsletter</h3>
      <p>Enter your email below to receive our weekly notes on markets and zone policy.</p>
      <div class="news-form"><div class="field">Your email address</div><span class="btn">Go</span></div>
      <p class="news-links">Unsubscribe &nbsp;|&nbsp; Privacy</p>
    </div>
    <div class="info">
      <h3>Need more info?</h3>
      <div class="field">Name</div>
      <div class="field">Email</div>
      <div class="field area">Message</div>
      <div class="info-submit"><span class="btn">Submit</span></div>
    </div>
  </footer>

  <div class="bottom">
    <span>Copyright © 2014 Valdo Capital</span>
    <div class="social"><span></span><span></span><span></span></div>
  </div>

</div>
</body>
</html>
```